House-share and Room Rental Website (With Focus on the Bedroom Landing Page)

Looking for website design for our House-share (executive accommodation) and room rental business.

Our company name is: Lodgivo could also be written as LodGivo or lodgivo. Either is fine .. just looking for a nice clean catchy logo to go with the design.

EXAMPLES
These are examples of other websites in this field that are doing well. this is a kind of baseline.
https://nestpartners-example.com.au/
https://www.bunkora-example.com/
https://www.dwelzy-example.com/
https://www.habiquo-example.net/
https://www.cohabiscout-example.com.au/

Our business model is to rent rooms to people looking for high-quality accommodation. We fill the gap between those looking to rent rooms and those with rooms to rent. However, our model is slightly different from those already on the market as we looking to fill a massive gap in the market delivering upmarket rooms for rent.(Executive Accommodation) also in the back end will be coupled with a self management process in the back end.

We offer executive style accommodation that stands out above the rest. With special extras like fire safety.. and management processes that create happier homes. We are looking for a web design package that can help us grow and scale our business. We need a design that is captivating

Our MAIN focus is having a room landing page that stands out from the rest... The core of our business will rely on the promotion of the rooms in a share house... so the whole design relies on the BEDROOM landing page to drive results.

Target Market(s)

We have 2 markets we are aiming at ... the first market is people offering rooms to rent who want the highest rental return. The second market is people looking to rent safe, high-quality rooms, in houses that are well managed and looked after.

Industry/Entity Type

Share Economy

Logo Text

LodGivo

Number of Pages Required

5+ page

Font styles to use
Sans Serif

Colors
3276b5

Requirements
Must have
• A messaging system whereby we can create direct communication between those offering rooms and those looking for rooms.
• A call to action that says " Schedule an Inspection"
• Landing page for promoting rooms
• A home page for showing stock.
• Profile page for those selling rooms
• Profile page for those looking for rooms.
• A scheduling calendar for booking inspections
Nice to have
• Pages where new residents can lock in a room.. pay bond and rents.. and sign contracts
• Notifications
• SMS capabilities in the backend.
Should not have
• No script or handwriting fonts.

```html
<!DOCTYPE html>
<html lang="en">
<head>
<meta charset="utf-8">
<title>Lodgivo — Executive Accommodation</title>
<link rel="stylesheet" href="https://fonts.googleapis.com/css2?family=Jost:wght@400;500;600&family=Lato:wght@400;700&display=swap">
<style>
:root{
  --navy:#2b2e8c;
  --navy-dark:#23266f;
  --ink:#1d1d1f;
  --text:#3a3a3a;
  --muted:#6d6d6d;
  --line:#dcdcdc;
  --page:#f5f5f5;
  --card:#ffffff;
  --footer:#1f1f1f;
  --footer-field:#3a3a3a;
  --button-dark:#444444;
}
*{box-sizing:border-box;margin:0;padding:0}
html,body{width:1200px;height:3364px;overflow:hidden}
body{background:var(--page);font-family:"Lato",sans-serif;color:var(--text);position:relative}
.abs{position:absolute}
h1,h2,h3,.heading{font-family:"Jost",sans-serif;font-weight:500;color:var(--ink)}

/* header */
.site-header{position:absolute;left:0;top:0;width:1200px;height:98px;background:#fff}
.menu-grid{left:78px;top:37px;width:24px;height:24px;display:grid;grid-template-columns:repeat(3,6px);gap:3px}
.menu-grid span{width:6px;height:6px;background:#333}
.lang{left:120px;top:39px;font-size:12px;color:#333;display:flex;align-items:center;gap:6px}
.lang i{display:block;width:14px;height:10px;background:#c9cfe6}
.brand{left:508px;top:24px;display:flex;align-items:center;gap:12px}
.brand-mark{width:40px;height:40px;background:var(--navy)}
.brand-name{font-family:"Lato",sans-serif;font-weight:700;font-size:28px;color:var(--navy);line-height:1}
.brand-tag{font-size:10px;color:var(--navy);letter-spacing:.5px;margin-top:3px}
.btn-post{left:918px;top:31px;width:127px;height:30px;background:var(--navy);color:#fff;border-radius:5px;font-size:12px;display:flex;align-items:center;justify-content:center}
.btn-login{left:1056px;top:31px;width:63px;height:30px;border:1px solid #bbb;border-radius:5px;font-size:12px;color:#333;display:flex;align-items:center;justify-content:center;background:#fff}

/* hero */
.hero{position:absolute;left:0;top:98px;width:1200px;height:557px;
  background:linear-gradient(100deg,#6f9ccf 0%,#a9c6e3 22%,#e9ecef 38%,#d3d6d8 55%,#8a9196 70%,#4f6b3d 86%,#2f4b26 100%)}
.hero-title{left:210px;top:332px;font-family:"Jost",sans-serif;font-size:33px;font-weight:500;color:#fff;line-height:1.25}
.hero-arrow{top:364px;width:12px;height:20px}
.search-panel{left:788px;top:202px;width:333px;height:378px;background:#fff;border-radius:8px;box-shadow:0 4px 18px rgba(0,0,0,.18);padding:22px 26px}
.search-panel h3{font-size:18px;text-align:center;margin-bottom:14px}
.field-label{font-size:11px;color:#333;margin:8px 0 5px}
.field{height:34px;border:1px solid var(--line);border-radius:4px;font-size:11px;color:#555;display:flex;align-items:center;justify-content:space-between;padding:0 10px}
.field-row{display:flex;gap:12px}
.field-row>div{flex:1}
.btn-search{margin-top:18px;height:34px;background:var(--navy);color:#fff;border-radius:5px;font-size:12px;display:flex;align-items:center;justify-content:center}

/* amenities */
.section-title{position:absolute;left:0;width:1200px;text-align:center;font-size:32px}
.amenity{position:absolute;top:780px;width:200px;text-align:center}
.amenity svg.icon{width:50px;height:50px;display:block;margin:0 auto}
.amenity h3{font-family:"Lato",sans-serif;font-size:17px;font-weight:400;margin-top:18px}
.amenity p{font-size:11.5px;line-height:15px;color:#333;margin:16px auto 0;width:170px}
.amenity .go{width:22px;height:22px;margin-top:18px}

/* recommended */
.tab{position:absolute;top:1140px;width:90px;text-align:center;font-size:17px;color:#444}
.tab svg{width:42px;height:42px;display:block;margin:0 auto 8px}
.tab.active{color:var(--navy);font-weight:700}
.listing{position:absolute;width:326px;height:412px;background:var(--card);box-shadow:0 1px 5px rgba(0,0,0,.08)}
.listing-photo{position:absolute;left:0;top:0;width:326px;height:215px}
.price{position:absolute;left:0;top:160px;height:34px;padding:0 20px 0 12px;background:var(--navy);color:#fff;font-weight:700;font-size:18px;display:flex;align-items:center;clip-path:polygon(0 0,88% 0,100% 50%,88% 100%,0 100%)}
.listing h4{position:absolute;left:18px;top:232px;font-size:15px;color:var(--navy);font-weight:700;line-height:18px}
.listing .rule{position:absolute;left:14px;right:14px;top:260px;border-top:1px solid #ececec}
.address{position:absolute;left:16px;top:272px;font-size:13px;line-height:16px;color:#444;display:flex;gap:8px;align-items:center}
.stats{position:absolute;left:18px;right:18px;top:306px;display:flex;justify-content:space-between}
.stat{width:80px;text-align:center;font-size:11px;line-height:14px;color:#555}
.stat .val{display:flex;gap:4px;justify-content:center;align-items:center;font-size:12px;line-height:16px;color:#333;margin-bottom:8px}
.browse{position:absolute;left:113px;top:368px;width:100px;height:28px;border-radius:5px;background:var(--button-dark);color:#fff;font-size:11px;display:flex;align-items:center;justify-content:center}
.btn-more{left:538px;top:2213px;width:128px;height:28px;background:var(--navy);color:#fff;border-radius:5px;font-size:11px;display:flex;align-items:center;justify-content:center}

/* testimonials */
.testimonial{position:absolute;top:2404px;width:294px;height:288px;background:#fff;text-align:center}
.avatar{width:100px;height:100px;border-radius:50%;margin:30px auto 0}
.testimonial h4{font-size:16px;font-weight:700;color:#222;margin-top:12px}
.testimonial .role{font-size:12px;color:var(--navy)}
.testimonial p{font-size:11.5px;line-height:15px;color:#444;width:200px;margin:12px auto 0}
.read{font-size:12px;color:#333;margin-top:14px;display:flex;justify-content:center;gap:6px;align-items:center}

/* newsletter */
.news-form{left:336px;top:2860px;width:570px;height:38px;background:#fff;display:flex;border-radius:3px}
.news-form span{flex:1;font-size:12px;color:#999;display:flex;align-items:center;padding-left:22px}
.news-form b{width:134px;background:var(--navy);color:#fff;font-size:13px;display:flex;align-items:center;justify-content:center;border-radius:3px}

/* footer */
.site-footer{position:absolute;left:0;top:2956px;width:1200px;height:350px;background:var(--footer);color:#e6e6e6}
.site-footer h5{font-family:"Jost",sans-serif;font-weight:500;font-size:15px;color:#fff}
.site-footer h5::after{content:"";display:block;width:70px;height:2px;background:#fff;margin-top:10px}
.links li{list-style:none;font-size:11px;line-height:24px;display:flex;gap:14px}
.contact-line{font-size:13px;line-height:21px;display:flex;gap:12px}
.qc-field{position:absolute;background:var(--footer-field);font-size:11px;color:#ddd;padding:6px 8px}
.social{display:flex;gap:10px}
.social i{display:block;width:22px;height:22px;border-radius:50%;border:1.5px solid #fff}
.footer-bar{position:absolute;left:0;top:3306px;width:1200px;height:58px;background:var(--navy);color:#fff;font-size:12px}
.cards{right:80px;top:20px;display:flex;gap:12px}
.cards i{display:block;width:32px;height:20px;background:#e9e9f2;border-radius:3px}
</style>
</head>
<body>

<header class="site-header">
  <div class="abs menu-grid"><span></span><span></span><span></span><span></span><span></span><span></span><span></span><span></span><span></span></div>
  <div class="abs lang"><i></i>Eng ▾</div>
  <div class="abs brand">
    <div class="brand-mark"></div>
    <div><div class="brand-name">Lodgivo</div><div class="brand-tag">Executive Accommodation</div></div>
  </div>
  <div class="abs btn-post">Post Your Room</div>
  <div class="abs btn-login">Log in</div>
</header>

<section class="hero" role="img" aria-label="Photo of a modern white house with glass walls, palm trees and greenery under a blue sky">
  <svg class="abs hero-arrow" style="left:32px;top:266px" viewBox="0 0 12 20"><path d="M10 2 2 10l8 8" fill="none" stroke="#fff" stroke-width="2"/></svg>
  <svg class="abs hero-arrow" style="left:1150px;top:266px" viewBox="0 0 12 20"><path d="M2 2l8 8-8 8" fill="none" stroke="#fff" stroke-width="2"/></svg>
</section>
<h1 class="abs hero-title">let us find Your Perfect<br>Room For Rent</h1>

<form class="abs search-panel">
  <h3>Find Your Room For Rent</h3>
  <div class="field-label">Where</div>
  <div class="field">Anywhere<svg width="12" height="14" viewBox="0 0 12 14"><path d="M6 13S1 8 1 5a5 5 0 0 1 10 0c0 3-5 8-5 8z" fill="none" stroke="#777"/><circle cx="6" cy="5" r="1.8" fill="#777"/></svg></div>
  <div class="field-row">
    <div><div class="field-label">Check in</div><div class="field"><span></span><svg width="14" height="14"><rect x="1" y="2" width="12" height="11" fill="none" stroke="#777"/><path d="M1 5h12" stroke="#777"/></svg></div></div>
    <div><div class="field-label">Check out</div><div class="field"><span></span><svg width="14" height="14"><rect x="1" y="2" width="12" height="11" fill="none" stroke="#777"/><path d="M1 5h12" stroke="#777"/></svg></div></div>
  </div>
  <div class="field-label">Category</div>
  <div class="field">Room For Rent<span>▾</span></div>
  <div class="field" style="margin-top:10px">Guests<span>▾</span></div>
  <div class="btn-search">Search</div>
</form>

<h2 class="section-title" style="top:706px">Public Amenities</h2>

<div class="amenity" style="left:57px">
  <svg class="icon" viewBox="0 0 50 50"><path d="M8 30l5-12h24l5 12v10H8z" fill="var(--navy)"/><circle cx="15" cy="40" r="4" fill="#fff"/><circle cx="35" cy="40" r="4" fill="#fff"/><rect x="15" y="21" width="20" height="7" fill="#fff"/></svg>
  <h3>Transport</h3>
  <p>Lorem Ipsum is simply is a text of the printinghas been ndustry's 1500s...</p>
  <svg class="go" viewBox="0 0 22 22"><circle cx="11" cy="11" r="9.5" fill="none" stroke="#333" stroke-width="1.5"/><path d="M6 11h9M12 7l4 4-4 4" fill="none" stroke="#333" stroke-width="1.5"/></svg>
</div>
<div class="amenity" style="left:279px">
  <svg class="icon" viewBox="0 0 50 50"><rect x="13" y="5" width="24" height="34" rx="5" fill="var(--navy)"/><rect x="17" y="11" width="16" height="10" fill="#fff"/><circle cx="19" cy="31" r="2.5" fill="#fff"/><circle cx="31" cy="31" r="2.5" fill="#fff"/><path d="M17 39l-5 7M33 39l5 7M10 46h30" stroke="var(--navy)" stroke-width="2.5"/></svg>
  <h3>Trains</h3>
  <p>Lorem Ipsum is simply is a text of the printinghas been ndustry's 1500s...</p>
  <svg class="go" viewBox="0 0 22 22"><circle cx="11" cy="11" r="9.5" fill="none" stroke="#333" stroke-width="1.5"/><path d="M6 11h9M12 7l4 4-4 4" fill="none" stroke="#333" stroke-width="1.5"/></svg>
</div>
<div class="amenity" style="left:499px">
  <svg class="icon" viewBox="0 0 50 50"><rect x="10" y="5" width="30" height="36" rx="5" fill="var(--navy)"/><rect x="14" y="12" width="22" height="13" fill="#fff"/><circle cx="17" cy="33" r="2.5" fill="#fff"/><circle cx="33" cy="33" r="2.5" fill="#fff"/><rect x="13" y="41" width="6" height="5" fill="var(--navy)"/><rect x="31" y="41" width="6" height="5" fill="var(--navy)"/></svg>
  <h3>Busses</h3>
  <p>Lorem Ipsum is simply is a text of the printinghas been ndustry's 1500s...</p>
  <svg class="go" viewBox="0 0 22 22"><circle cx="11" cy="11" r="9.5" fill="none" stroke="#333" stroke-width="1.5"/><path d="M6 11h9M12 7l4 4-4 4" fill="none" stroke="#333" stroke-width="1.5"/></svg>
</div>
<div class="amenity" style="left:717px">
  <svg class="icon" viewBox="0 0 50 50"><circle cx="25" cy="25" r="19" fill="none" stroke="var(--navy)" stroke-width="2.5"/><path d="M25 34s-8-8-8-14a8 8 0 0 1 16 0c0 6-8 14-8 14z" fill="var(--navy)"/><circle cx="25" cy="20" r="3" fill="#fff"/></svg>
  <h3>Location</h3>
  <p>Lorem Ipsum is simply is a text of the printinghas been ndustry's 1500s...</p>
  <svg class="go" viewBox="0 0 22 22"><circle cx="11" cy="11" r="9.5" fill="none" stroke="#333" stroke-width="1.5"/><path d="M6 11h9M12 7l4 4-4 4" fill="none" stroke="#333" stroke-width="1.5"/></svg>
</div>
<div class="amenity" style="left:936px">
  <svg class="icon" viewBox="0 0 50 50"><path d="M5 10l13-4 14 4 13-4v34l-13 4-14-4-13 4z" fill="none" stroke="var(--navy)" stroke-width="2.5"/><path d="M18 6v34M32 10v34" stroke="var(--navy)" stroke-width="2.5"/><path d="M33 28s-5-5-5-9a5 5 0 0 1 10 0c0 4-5 9-5 9z" fill="var(--navy)"/></svg>
  <h3>MAP</h3>
  <p>Lorem Ipsum is simply is a text of the printinghas been ndustry's 1500s...</p>
  <svg class="go" viewBox="0 0 22 22"><circle cx="11" cy="11" r="9.5" fill="none" stroke="#333" stroke-width="1.5"/><path d="M6 11h9M12 7l4 4-4 4" fill="none" stroke="#333" stroke-width="1.5"/></svg>
</div>

<h2 class="section-title" style="top:1056px">Recommended for you</h2>

<div class="tab active" style="left:266px"><svg viewBox="0 0 42 42"><g fill="var(--navy)"><rect x="6" y="6" width="8" height="8"/><rect x="17" y="6" width="8" height="8"/><rect x="28" y="6" width="8" height="8"/><rect x="6" y="17" width="8" height="8"/><rect x="17" y="17" width="8" height="8"/><rect x="28" y="17" width="8" height="8"/><rect x="6" y="28" width="8" height="8"/><rect x="17" y="28" width="8" height="8"/><rect x="28" y="28" width="8" height="8"/></g></svg>All</div>
<div class="tab" style="left:410px"><svg viewBox="0 0 42 42"><path d="M4 20 21 5l17 15M9 16v21h24V16M17 37V26h8v11" fill="none" stroke="#333" stroke-width="2"/></svg>House</div>
<div class="tab" style="left:558px"><svg viewBox="0 0 42 42"><rect x="11" y="4" width="20" height="34" fill="none" stroke="#333" stroke-width="2"/><circle cx="26" cy="22" r="1.8" fill="#333"/></svg>Room</div>
<div class="tab" style="left:707px"><svg viewBox="0 0 42 42"><path d="M4 14 21 4l17 10v24H4z" fill="none" stroke="#333" stroke-width="2"/><circle cx="15" cy="21" r="3.5" fill="none" stroke="#333" stroke-width="2"/><circle cx="27" cy="21" r="3.5" fill="none" stroke="#333" stroke-width="2"/><path d="M9 33c0-4 3-6 6-6s6 2 6 6M21 33c0-4 3-6 6-6s6 2 6 6" fill="none" stroke="#333" stroke-width="2"/></svg>Roomate</div>
<div class="tab" style="left:856px"><svg viewBox="0 0 42 42"><path d="M4 16 21 5l17 11v22H4z" fill="none" stroke="#333" stroke-width="2"/><circle cx="21" cy="20" r="3.5" fill="none" stroke="#333" stroke-width="2"/><path d="M14 34c0-5 3-8 7-8s7 3 7 8" fill="none" stroke="#333" stroke-width="2"/></svg>Tenant</div>

<!-- listing cards -->
<article class="listing" style="left:81px;top:1276px">
  <div class="listing-photo" role="img" aria-label="Photo of a bedroom with a timber wall, grey bedding and a window" style="background:linear-gradient(135deg,#7b5a3e,#b9a592 45%,#8c9a98)"></div>
  <div class="price">$250</div>
  <h4>Luxurious &amp; Stunning Room</h4><div class="rule"></div>
  <div class="address"><svg width="11" height="14" viewBox="0 0 12 14"><path d="M6 13S1 8 1 5a5 5 0 0 1 10 0c0 3-5 8-5 8z" fill="none" stroke="#555"/><circle cx="6" cy="5" r="1.6" fill="#555"/></svg>17 Larkspur Lane, Wendaree, Australia</div>
  <div class="stats"><div class="stat"><div class="val">▢ 2</div>Rooms</div><div class="stat"><div class="val">▭ 4</div>Bedrooms</div><div class="stat"><div class="val">◛ 2</div>Bath</div></div>
  <div class="browse">Browse</div>
</article>
<article class="listing" style="left:437px;top:1276px">
  <div class="listing-photo" role="img" aria-label="Photo of a house among tall pine trees on a green lawn" style="background:linear-gradient(180deg,#c9d6de,#5f7b52 45%,#3e5a2f)"></div>
  <div class="price">$250</div>
  <h4>Luxurious &amp; Stunning Room</h4><div class="rule"></div>
  <div class="address"><svg width="11" height="14" viewBox="0 0 12 14"><path d="M6 13S1 8 1 5a5 5 0 0 1 10 0c0 3-5 8-5 8z" fill="none" stroke="#555"/><circle cx="6" cy="5" r="1.6" fill="#555"/></svg>17 Larkspur Lane, Wendaree, Australia</div>
  <div class="stats"><div class="stat"><div class="val">▢ 2</div>Rooms</div><div class="stat"><div class="val">▭ 4</div>Bedrooms</div><div class="stat"><div class="val">◛ 2</div>Bath</div></div>
  <div class="browse">Browse</div>
</article>
<article class="listing" style="left:794px;top:1276px">
  <div class="listing-photo" role="img" aria-label="Photo of a modern dark building facade against a blue sky" style="background:linear-gradient(135deg,#2d3f8a,#3c4f97 40%,#4a4a4f 70%,#7b7e84)"></div>
  <div class="price">$250</div>
  <h4>Luxurious &amp; Stunning Room</h4><div class="rule"></div>
  <div class="address"><svg width="11" height="14" viewBox="0 0 12 14"><path d="M6 13S1 8 1 5a5 5 0 0 1 10 0c0 3-5 8-5 8z" fill="none" stroke="#555"/><circle cx="6" cy="5" r="1.6" fill="#555"/></svg>17 Larkspur Lane, Wendaree, Australia</div>
  <div class="stats"><div class="stat"><div class="val">▢ 2</div>Rooms</div><div class="stat"><div class="val">▭ 4</div>Bedrooms</div><div class="stat"><div class="val">◛ 2</div>Bath</div></div>
  <div class="browse">Browse</div>
</article>
<article class="listing" style="left:81px;top:1738px">
  <div class="listing-photo" role="img" aria-label="Photo of a canopy bed with white drapes and orange cushions" style="background:linear-gradient(180deg,#efe9e2,#dccfc2 55%,#b9774a)"></div>
  <div class="price">$250</div>
  <h4>Luxurious &amp; Stunning Room</h4><div class="rule"></div>
  <div class="address"><svg width="11" height="14" viewBox="0 0 12 14"><path d="M6 13S1 8 1 5a5 5 0 0 1 10 0c0 3-5 8-5 8z" fill="none" stroke="#555"/><circle cx="6" cy="5" r="1.6" fill="#555"/></svg>17 Larkspur Lane, Wendaree, Australia</div>
  <div class="stats"><div class="stat"><div class="val">▢ 2</div>Rooms</div><div class="stat"><div class="val">▭ 4</div>Bedrooms</div><div class="stat"><div class="val">◛ 2</div>Bath</div></div>
  <div class="browse">Browse</div>
</article>
<article class="listing" style="left:437px;top:1738px">
  <div class="listing-photo" role="img" aria-label="Photo of a living room with a white sofa, blue cushions and wall art" style="background:linear-gradient(180deg,#d7dcdf,#eef0ef 50%,#2f5f78)"></div>
  <div class="price">$250</div>
  <h4 style="font-weight:400">Luxurious &amp; Stunning Room</h4><div class="rule"></div>
  <div class="address"><svg width="11" height="14" viewBox="0 0 12 14"><path d="M6 13S1 8 1 5a5 5 0 0 1 10 0c0 3-5 8-5 8z" fill="none" stroke="#555"/><circle cx="6" cy="5" r="1.6" fill="#555"/></svg>17 Larkspur Lane, Wendaree, Australia</div>
  <div class="stats"><div class="stat"><div class="val">▢ 2</div>Rooms</div><div class="stat"><div class="val">▭ 4</div>Bedrooms</div><div class="stat"><div class="val">◛ 2</div>Bath</div></div>
  <div class="browse">Browse</div>
</article>
<article class="listing" style="left:794px;top:1738px">
  <div class="listing-photo" role="img" aria-label="Photo of a lit cabin in snowy pine woods at dusk" style="background:linear-gradient(180deg,#5a6470,#3b3f45 45%,#a0623a 65%,#d9dde2)"></div>
  <div class="price">$250</div>
  <h4>Luxurious &amp; Stunning Room</h4><div class="rule"></div>
  <div class="address"><svg width="11" height="14" viewBox="0 0 12 14"><path d="M6 13S1 8 1 5a5 5 0 0 1 10 0c0 3-5 8-5 8z" fill="none" stroke="#555"/><circle cx="6" cy="5" r="1.6" fill="#555"/></svg>17 Larkspur Lane, Wendaree, Australia</div>
  <div class="stats"><div class="stat"><div class="val">▢ 2</div>Rooms</div><div class="stat"><div class="val">▭ 4</div>Bedrooms</div><div class="stat"><div class="val">◛ 2</div>Bath</div></div>
  <div class="browse">Browse</div>
</article>

<div class="abs btn-more">View More</div>

<div class="abs" style="left:0;top:2306px;width:1200px;text-align:center;font-size:12px;color:#222">Testimonials</div>
<h2 class="section-title" style="top:2328px">What Client Say</h2>

<div class="testimonial" style="left:117px">
  <div class="avatar" role="img" aria-label="Portrait photo of the client" style="background:radial-gradient(circle,#8b7565,#3a3330)"></div>
  <h4>Marcus</h4><div class="role">Director</div>
  <p>Lorem Ipsum is simply dummy of the printing and typesetting Lorem Ipsum industry.</p>
  <div class="read">Read More... <svg width="12" height="12" viewBox="0 0 22 22"><circle cx="11" cy="11" r="9.5" fill="none" stroke="#333" stroke-width="2"/><path d="M6 11h9M12 7l4 4-4 4" fill="none" stroke="#333" stroke-width="2"/></svg></div>
</div>
<div class="testimonial" style="left:453px">
  <div class="avatar" role="img" aria-label="Portrait photo of the client" style="background:radial-gradient(circle,#c9a58c,#3f6f8f)"></div>
  <h4>Oliver</h4><div class="role">Director</div>
  <p>Lorem Ipsum is simply dummy of the printing and typesetting Lorem Ipsum industry.</p>
  <div class="read">Read More... <svg width="12" height="12" viewBox="0 0 22 22"><circle cx="11" cy="11" r="9.5" fill="none" stroke="#333" stroke-width="2"/><path d="M6 11h9M12 7l4 4-4 4" fill="none" stroke="#333" stroke-width="2"/></svg></div>
</div>
<div class="testimonial" style="left:783px">
  <div class="avatar" role="img" aria-label="Portrait photo of the client" style="background:radial-gradient(circle,#a07b63,#2a2a2a)"></div>
  <h4>Tobias</h4><div class="role">Director</div>
  <p>Lorem Ipsum is simply dummy of the printing and typesetting Lorem Ipsum industry.</p>
  <div class="read">Read More... <svg width="12" height="12" viewBox="0 0 22 22"><circle cx="11" cy="11" r="9.5" fill="none" stroke="#333" stroke-width="2"/><path d="M6 11h9M12 7l4 4-4 4" fill="none" stroke="#333" stroke-width="2"/></svg></div>
</div>

<h2 class="section-title" style="top:2772px;font-size:25px">Subscribe To Our Newsletter</h2>
<div class="abs" style="left:0;top:2814px;width:1200px;text-align:center;font-size:12px;color:#333">To Receive The latest News And Update</div>
<div class="abs news-form"><span>Your E-Mail</span><b>Submit</b></div>

<footer class="site-footer">
  <div class="abs" style="left:79px;top:88px;display:flex;align-items:center;gap:10px">
    <div style="width:40px;height:40px;border:2px solid #fff;border-radius:50%"></div>
    <div><div style="font-weight:700;font-size:28px;line-height:1;color:#fff">Lodgivo</div><div style="font-size:10px;color:#fff;margin-top:3px">Executive Accommodation</div></div>
  </div>
  <p class="abs" style="left:79px;top:158px;width:220px;font-size:13px;line-height:20px">Lorem Ipsum is simply dummy text of the printing and types tysletting industry...</p>
  <div class="abs social" style="left:79px;top:252px"><i></i><i></i><i></i><i></i><i></i></div>

  <div class="abs" style="left:372px;top:77px">
    <h5>Useful links</h5>
    <ul class="links" style="margin-top:18px">
      <li><span>›</span>Login</li><li><span>›</span>Register</li><li><span>›</span>My Profile</li><li><span>›</span>My Subscription</li><li><span>›</span>Privacy policy</li><li><span>›</span>Terms &amp; Conditions</li>
    </ul>
  </div>

  <div class="abs" style="left:578px;top:77px">
    <h5>Contact us</h5>
    <div class="contact-line" style="margin-top:22px"><span>⌂</span><span>8 Quillon Court, Marrowby<br>Western Australia.<br>ZipCode: 60417</span></div>
    <div class="contact-line" style="margin-top:8px"><span>☎</span><span>0400 555 218</span></div>
    <div class="contact-line" style="margin-top:8px"><span>✉</span><span>hello@lodgivo.example</span></div>
  </div>

  <div class="abs" style="left:888px;top:77px"><h5>Quick Contact</h5></div>
  <div class="qc-field" style="left:888px;top:144px;width:112px;height:26px">Name</div>
  <div class="qc-field" style="left:1007px;top:144px;width:112px;height:26px">Phone</div>
  <div class="qc-field" style="left:888px;top:182px;width:231px;height:56px">Message</div>
  <div class="abs" style="left:996px;top:250px;width:123px;height:32px;background:var(--navy);color:#fff;font-size:13px;font-weight:700;display:flex;align-items:center;justify-content:center">Send</div>
</footer>

<div class="footer-bar">
  <div class="abs" style="left:79px;top:22px">CopyRight © 2019 Lodgivo. All Right Reserve</div>
  <div class="abs cards"><i></i><i></i><i></i><i></i><i></i></div>
</div>

</body>
</html>
```